Elegant Business Card for Technology Company

Client is a supplier of innovative industrial communications and automation equipment since 2002. This contest is to gather fresh ideas for a redesign of the existing business card. Client is looking for design that best communicates tagline "Industrial Networking and Computing Specialist".

Design submissions should look modern, clean, elegant and professional. It should not be cluttered. Use white as the primary colour. Orange and black as secondary colour. Refer to jpeg File 1 on the current design.

Fonts used by Client used include Arial Regular, Arial Black, Roboto Regular, Roboto Black and Lato.

The winning design will be sent for offset printing using super white 250gsm artcard paper (open for suggestions).

Target Market(s)

System Engineers, Project Managers, Purchasing Managers from companies providing engineering services for Smart Cities.

Industry/Entity Type

Information Technology

Contact Information for Business Card

Refer to PDF File 3 for Business Card Details. Priority of short contact information would be as follows Name > Job Title > Email > Mobile > Web > Tel > Fax > Business Address >UEN (UEN represents company registration number)

Font styles to use
Sans Serif

Colors
ffffff
f37122
000000
5c5c5c

Requirements
Must have
• Refer to AI File 2 (Company Logo) & PDF File 3 (Information on Namecard)
Should not have
• No QR codes
• No Social Media Icons
• Do not create full Black or Orange colour background

```html
<!DOCTYPE html>
<html lang="en">
<head>
<meta charset="utf-8">
<title>KVR Business Card</title>
<link rel="stylesheet" href="https://fonts.googleapis.com/css2?family=Roboto:wght@400;500;900&display=swap">
<style>
  :root {
    --white: #ffffff;
    --orange: #f37122;
    --orange-deep: #c8561a;
    --black: #000000;
    --grey: #5c5c5c;
    --rule: #d9d9d9;
    --backdrop: #ecebe8;
  }
  * { box-sizing: border-box; margin: 0; padding: 0; }
  html, body {
    width: 1200px; height: 950px; overflow: hidden;
    background: var(--backdrop);
    font-family: "Roboto", Arial, sans-serif;
  }
  .canvas { position: relative; width: 1200px; height: 950px; }

  .card {
    position: absolute; left: 250px; width: 700px; height: 420px;
    border-radius: 4px; overflow: hidden;
    box-shadow: 0 10px 28px rgba(0,0,0,0.18);
  }

  /* Back side */
  .card-back {
    top: 30px;
    background: linear-gradient(135deg, var(--orange) 0%, #e8691f 55%, var(--orange-deep) 100%);
    color: var(--white);
    text-align: center;
  }
  .back-disc {
    position: absolute; left: 290px; top: 60px;
    width: 120px; height: 120px; border-radius: 50%;
    background: var(--white); opacity: 0.92;
  }
  .tagline {
    position: absolute; left: 0; right: 0; top: 215px;
    font-size: 19px; line-height: 30px; letter-spacing: 0.5px;
  }
  .tagline .lead { font-weight: 500; font-size: 21px; }

  /* Front side */
  .card-front { top: 490px; background: var(--white); }
  .brand {
    position: absolute; left: 60px; top: 80px;
    display: flex; align-items: center; gap: 16px;
  }
  .brand-disc {
    width: 110px; height: 110px; border-radius: 50%;
    background: var(--orange);
  }
  .brand-name {
    font-weight: 900; font-size: 66px; color: var(--black); letter-spacing: -1px;
  }
  .divider {
    position: absolute; left: 372px; top: 70px; width: 1px; height: 230px;
    background: var(--rule);
  }
  .contact { position: absolute; left: 398px; top: 72px; color: var(--grey); }
  .person-name { color: var(--orange); font-size: 24px; font-weight: 500; }
  .job-title { color: var(--black); font-size: 16px; margin-top: 2px; }
  .address { font-size: 15px; line-height: 20px; margin-top: 14px; }
  .lines { list-style: none; margin-top: 6px; font-size: 15px; line-height: 23px; }
  .lines li { display: flex; align-items: center; gap: 8px; }
  .lines svg { width: 14px; height: 14px; fill: var(--orange); flex: none; }

  .web-band {
    position: absolute; left: 0; top: 318px; width: 440px; height: 36px;
    background: var(--black); color: var(--white);
    font-size: 15px; letter-spacing: 6px;
    display: flex; align-items: center; padding-left: 110px;
  }
  .accent-band {
    position: absolute; left: 480px; top: 368px; width: 220px; height: 22px;
    background: var(--orange);
  }
  .accent-disc {
    position: absolute; left: 462px; top: 356px; width: 46px; height: 46px;
    border-radius: 50%; background: var(--grey);
  }
</style>
</head>
<body>
<main class="canvas">
  <section class="card card-back" aria-label="Card back">
    <div class="back-disc"></div>
    <p class="tagline">
      <span class="lead">Industrial Networking &amp; Computing Specialist</span><br>
      Ethernet / Wireless / Cellular<br>
      Routing / Serial / Fieldbus Connectivity<br>
      SCADA &amp; Remote Automation
    </p>
  </section>

  <section class="card card-front" aria-label="Card front">
    <div class="brand">
      <div class="brand-disc"></div>
      <span class="brand-name">KVR</span>
    </div>
    <div class="divider"></div>
    <div class="contact">
      <p class="person-name">Daniel Koh</p>
      <p class="job-title">Sales Manager</p>
      <p class="address">24 Harlow Lane Eastgate Park<br>#02-15 (Lobby B)<br>Singapore 400123</p>
      <ul class="lines">
        <li><svg viewBox="0 0 16 16" aria-hidden="true"><path d="M3 1h3l1.5 4-2 1.3a9 9 0 0 0 4.2 4.2L11 8.5l4 1.5v3a2 2 0 0 1-2 2A13 13 0 0 1 1 3a2 2 0 0 1 2-2z"/></svg>+65 6000 1240</li>
        <li><svg viewBox="0 0 16 16" aria-hidden="true"><path d="M4 0h8a1 1 0 0 1 1 1v14a1 1 0 0 1-1 1H4a1 1 0 0 1-1-1V1a1 1 0 0 1 1-1zm1 2v10h6V2zm3 11a1 1 0 1 0 0 2 1 1 0 0 0 0-2z"/></svg>+65 8000 4321</li>
        <li><svg viewBox="0 0 16 16" aria-hidden="true"><path d="M4 0h8v4H4zM1 5h14v7h-3v4H4v-4H1zm4 5v4h6v-4z"/></svg>+65 6000 1387</li>
        <li><svg viewBox="0 0 16 16" aria-hidden="true"><path d="M0 3h16v1L8 9 0 4zm0 3l8 5 8-5v7H0z"/></svg>sales@kvrnet.com.sg</li>
      </ul>
    </div>
    <div class="web-band">www.kvrnet.com.sg</div>
    <div class="accent-band"></div>
    <div class="accent-disc"></div>
  </section>
</main>
</body>
</html>
```